Kelmo website design on shopify

Job Description:
As a web designer for Kelmo, you will be the driving force behind designing and developing our new e-commerce website. Your responsibility will be to create an attractive, functional, and intuitive online shopping experience where customers can effortlessly discover and purchase high-quality supplements such as pre-workout, creatine, and protein shakes. Your design will play a crucial role in enhancing our brand and engaging our target audience.

```html
<!DOCTYPE html>
<html lang="en">
<head>
<meta charset="utf-8">
<title>Kelmo — Supplements Store</title>
<link rel="stylesheet" href="https://fonts.googleapis.com/css2?family=Michroma&family=Inter:wght@400;500;600;700&display=swap">
<style>
:root{
  --purple:#6c1f80;
  --purple-dark:#4e1260;
  --lavender:#e9dcea;
  --lavender-soft:#efe5f0;
  --ink:#222;
  --text:#3a3a3a;
  --white:#fff;
  --black:#000;
  --line:#b9a9bd;
  --count-bg:#f1f6d9;
}
*{box-sizing:border-box;margin:0;padding:0}
html,body{width:1200px;height:5080px;overflow:hidden}
body{position:relative;background:var(--white);font-family:"Inter",sans-serif;color:var(--text)}
.abs{position:absolute}
.display{font-family:"Michroma",sans-serif;color:var(--purple);letter-spacing:1px;text-transform:uppercase}
.photo{position:absolute;border-radius:10px}
.center{text-align:center}

/* top bar */
.topbar{left:0;top:0;width:1200px;height:63px;background:var(--black);color:var(--white);font-size:16px;font-weight:500;display:flex;align-items:center;justify-content:center}

/* header */
.brand{display:flex;align-items:center;gap:10px}
.brand-dot{width:34px;height:34px;border-radius:50%;background:var(--purple)}
.brand-name{font-family:"Inter",sans-serif;font-weight:600;font-size:38px;color:var(--purple)}
.nav{left:423px;top:110px;display:flex;gap:26px;font-size:16px;font-weight:500;color:var(--ink)}
.icons{left:962px;top:108px;display:flex;gap:26px}

/* services */
.services{left:0;top:174px;width:1200px;height:691px;background:var(--lavender)}
.title-lg{font-size:24px}
.svc-title{font-size:20px;width:311px}
.svc-text{font-size:16px;line-height:32px;width:311px;color:var(--ink)}

/* features */
.feature{width:320px;text-align:center}
.feature h3{font-family:"Michroma",sans-serif;color:var(--purple);font-size:19px;font-weight:400;margin-top:22px;letter-spacing:1px}
.feature p{font-size:16px;margin-top:20px;color:var(--ink)}

/* products */
.card{position:absolute;width:233px}
.card .img{height:275px;border-radius:6px}
.card h4{font-size:19px;font-weight:600;color:var(--purple);margin:30px 0 0 4px}
.card .price{font-size:19px;font-weight:600;color:var(--ink);margin:16px 0 0 4px}

/* banners */
.banner{left:0;width:1200px;height:429px}
.banner-copy{right:108px;text-align:right;color:var(--white)}
.banner-copy h2{font-family:"Michroma",sans-serif;font-weight:400;font-size:20px;letter-spacing:1px}
.banner-copy p{font-size:16px;line-height:32px;margin-top:22px}
.btn-outline{display:inline-flex;align-items:center;justify-content:center;border:2px solid currentColor;font-family:"Michroma",sans-serif;font-size:14px;letter-spacing:1px}

/* countdown */
.countdown{left:754px;top:3885px;width:334px;height:79px;background:var(--count-bg);display:flex;justify-content:space-around;align-items:center;font-family:"Michroma",sans-serif;font-size:13px;color:var(--ink);text-align:center}
.countdown span{display:block;line-height:30px}

/* forms */
.field{border:1.5px solid var(--ink);background:var(--white);font-size:15px;font-weight:500;color:var(--ink);display:flex;align-items:center;padding-left:20px}
.btn-plain{border:1.5px solid var(--ink);background:var(--white);font-size:15px;font-weight:500;color:var(--ink);display:flex;align-items:center;justify-content:center}

/* footer */
.footer{left:0;top:4679px;width:1200px;height:401px;background:var(--lavender)}
.foot-title{font-size:17px}
.foot-link{font-size:13px;color:var(--ink)}
.social{width:30px;height:30px;border-radius:4px;background:var(--purple)}
.pay{width:30px;height:16px;border-radius:3px}
</style>
</head>
<body>

<div class="abs topbar">FREE SHIPPING ABOVE $100</div>

<!-- header -->
<div class="abs brand" style="left:110px;top:98px"><div class="brand-dot"></div><div class="brand-name">Kelmo</div></div>
<nav class="abs nav"><span>HOME</span><span>PRODUCTS</span><span>ABOUT US</span><span>CONTACT</span></nav>
<div class="abs icons">
  <svg width="22" height="22" viewBox="0 0 24 24" fill="none" stroke="#222" stroke-width="2"><circle cx="10" cy="10" r="6"/><path d="M15 15l5 5"/></svg>
  <svg width="22" height="22" viewBox="0 0 24 24" fill="none" stroke="#222" stroke-width="2"><circle cx="12" cy="12" r="9"/><circle cx="12" cy="10" r="3"/><path d="M6 18c3-3 9-3 12 0"/></svg>
  <svg width="22" height="22" viewBox="0 0 24 24" fill="none" stroke="#222" stroke-width="2"><path d="M6 8h12l-1 12H7z"/><path d="M9 8V6a3 3 0 0 1 6 0v2"/></svg>
</div>

<!-- services -->
<section class="abs services"></section>
<h2 class="abs display title-lg center" style="left:0;top:230px;width:1200px">Our Services</h2>

<h3 class="abs display svc-title center" style="left:110px;top:313px">Pre-Workout</h3>
<p class="abs svc-text center" style="left:110px;top:350px">Sed ut perspiciatis unde omnis iste natus error sit voluptatem</p>
<div class="photo" role="img" aria-label="Woman stretching on a yoga mat at home" style="left:110px;top:436px;width:311px;height:346px;background:linear-gradient(160deg,#d8d2c8,#9a8f86 55%,#5b4a4a)"></div>

<div class="photo" role="img" aria-label="Scoop of creatine powder over a dark shaker" style="left:444px;top:322px;width:310px;height:345px;background:linear-gradient(150deg,#3b3b3b,#1e1e1e 60%,#6d655c)"></div>
<h3 class="abs display svc-title center" style="left:444px;top:685px;width:310px">Creatine</h3>
<p class="abs svc-text center" style="left:444px;top:723px;width:310px">Sed ut perspiciatis unde omnis iste natus error sit voluptatem</p>

<h3 class="abs display svc-title center" style="left:776px;top:313px">Protein Shakes</h3>
<p class="abs svc-text center" style="left:776px;top:350px">Sed ut perspiciatis unde omnis iste natus error sit voluptatem</p>
<div class="photo" role="img" aria-label="Man drinking a protein shake after training" style="left:776px;top:436px;width:312px;height:346px;background:linear-gradient(160deg,#8d8a86,#5a5550 50%,#2a2626)"></div>

<!-- features -->
<div class="abs feature" style="left:106px;top:955px">
  <svg width="96" height="66" viewBox="0 0 96 66" fill="none" stroke="#6c1f80" stroke-width="2.5"><rect x="10" y="6" width="48" height="38"/><path d="M58 18h16l12 14v12H58"/><circle cx="26" cy="50" r="7"/><circle cx="72" cy="50" r="7"/><path d="M24 24l7 7 13-13"/><path d="M2 20h8M4 30h6"/></svg>
  <h3>Free Shipping</h3><p>Sed ut perspiciatis iste</p>
</div>
<div class="abs feature" style="left:440px;top:955px">
  <svg width="66" height="66" viewBox="0 0 66 66" fill="none" stroke="#6c1f80" stroke-width="2.5"><path d="M10 20l22-10 22 10v24L32 56 10 44z"/><path d="M10 20l22 10 22-10M32 30v26M21 15l22 10"/><path d="M40 48a10 10 0 1 0 14-12"/><path d="M54 30v6h-6"/></svg>
  <h3>Return Policy</h3><p>Sed ut perspiciatis iste</p>
</div>
<div class="abs feature" style="left:760px;top:955px">
  <svg width="70" height="66" viewBox="0 0 70 66" fill="none" stroke="#6c1f80" stroke-width="2.5"><path d="M4 26h52l-6 30H12z"/><path d="M16 26l8-14M44 26l-8-14"/><path d="M20 34v14M30 34v14M40 34v14"/><circle cx="56" cy="14" r="9"/><path d="M52 14l3 3 5-6"/></svg>
  <h3>Checkout</h3><p>Sed ut perspiciatis iste</p>
</div>

<!-- feature story -->
<div class="abs" role="img" aria-label="Man pouring protein powder into a shaker bottle" style="left:110px;top:1194px;width:336px;height:488px;background:linear-gradient(170deg,#6a6a70,#4a4a52 55%,#7a5a40)"></div>
<svg class="abs" style="left:385px;top:1222px" width="36" height="36" viewBox="0 0 36 36"><circle cx="18" cy="18" r="17" fill="#6c1f80"/><circle cx="18" cy="18" r="10" fill="none" stroke="#fff" stroke-width="2"/><path d="M18 13v10M13 18h10" stroke="#fff" stroke-width="2"/></svg>
<h2 class="abs display" style="left:525px;top:1190px;font-size:20px">Lorem Ipsum</h2>
<p class="abs" style="left:527px;top:1232px;font-size:16px;color:var(--ink)">Sed ut perspiciatis iste natus error sit voluptatem accusantium</p>
<div class="abs" role="img" aria-label="Supplement capsules, powder and dumbbells on a dark stone surface" style="left:525px;top:1285px;width:563px;height:383px;background:linear-gradient(140deg,#6e6e6e,#3d3d3d 50%,#242424)"></div>

<!-- new arrivals -->
<h2 class="abs display center" style="left:0;top:1770px;width:1200px;font-size:20px">New Arrivals</h2>
<p class="abs center" style="left:0;top:1814px;width:1200px;font-size:16px;color:var(--ink)">Sed ut perspiciatis iste natus error sit voluptatem accusantium</p>

<div class="card" style="left:122px;top:1879px"><div class="img" role="img" aria-label="Woman holding a supplement bottle in a kitchen" style="background:linear-gradient(160deg,#ece8e4,#b9aea6)"></div><h4>LOREM IPSUM</h4><p class="price">$56.9</p></div>
<div class="card" style="left:363px;top:1879px"><div class="img" role="img" aria-label="Whey protein tubs and bottles" style="background:linear-gradient(160deg,#2a2a2a,#8a8580 60%,#d9d4cf)"></div><h4>LOREM IPSUM</h4><p class="price">$46.3</p></div>
<div class="card" style="left:604px;top:1879px"><div class="img" role="img" aria-label="Dark protein tub with shaker and pills" style="background:linear-gradient(160deg,#1c1d2c,#3b3c52 60%,#a8a39c)"></div><h4>LOREM IPSUM</h4><p class="price">$16.9</p></div>
<div class="card" style="left:845px;top:1879px"><div class="img" role="img" aria-label="Scoop of chocolate protein powder" style="background:linear-gradient(160deg,#e6d6c8,#b58a6c 60%,#8a624a)"></div><h4>LOREM IPSUM</h4><p class="price">$96.1</p></div>

<div class="card" style="left:122px;top:2292px"><div class="img" role="img" aria-label="Pile of herbal capsules and tablets" style="background:linear-gradient(160deg,#b8a070,#6f8a4a 55%,#3f5a30)"></div><h4>LOREM IPSUM</h4><p class="price">$23.8</p></div>
<div class="card" style="left:363px;top:2292px"><div class="img" role="img" aria-label="Assorted vitamin capsules on a white surface" style="background:linear-gradient(160deg,#f0efec,#e3d9a8 60%,#d8b860)"></div><h4>LOREM IPSUM</h4><p class="price">$56.8</p></div>
<div class="card" style="left:604px;top:2292px"><div class="img" role="img" aria-label="Woman taking a supplement capsule" style="background:linear-gradient(160deg,#7c9a5a,#a07a6a 55%,#5a3e40)"></div><h4>LOREM IPSUM</h4><p class="price">$23.8</p></div>
<div class="card" style="left:845px;top:2292px"><div class="img" role="img" aria-label="Blank black supplement jar with white label" style="background:linear-gradient(160deg,#5a5a5a,#7a7a7a 55%,#4a4a4a)"></div><h4>LOREM IPSUM</h4><p class="price">$45.9</p></div>

<!-- dark banner -->
<div class="abs banner" role="img" aria-label="Supplement tubs and dumbbells on a dark gym floor" style="top:2750px;background:linear-gradient(100deg,#2a2a30,#4a4a50 45%,#3a3a40 75%,#2e2e34)"></div>
<div class="abs banner-copy" style="top:2900px">
  <h2>Lorem Ipsum</h2>
  <p>Sed ut perspiciatis iste natus error sit<br>voluptatem accusantium</p>
  <div class="btn-outline" style="width:180px;height:63px;margin-top:23px;color:var(--white)">SHOP NOW</div>
</div>

<!-- feature block -->
<div class="abs" style="left:110px;top:3279px;width:490px;height:328px;background:var(--lavender-soft)"></div>
<h2 class="abs display" style="left:140px;top:3310px;font-size:20px">Lorem Ipsum</h2>
<p class="abs" style="left:140px;top:3356px;width:420px;font-size:16px;line-height:32.5px;color:var(--ink)">Lorem ipsum dolor sit amet, consectetur adipiscing elit, sed do eiusmod tempor incididunt ut labore et dolore magna aliqua. Ut enim ad minim veniam, quis nostrud</p>
<div class="abs btn-outline" style="left:140px;top:3508px;width:152px;height:55px;font-size:11px;color:var(--purple)">SHOP NOW</div>
<div class="abs" role="img" aria-label="Amber bottle spilling golden softgel capsules on wood" style="left:600px;top:3261px;width:488px;height:346px;background:linear-gradient(150deg,#b89670,#8a6440 55%,#c8a050)"></div>

<!-- countdown banner -->
<div class="abs banner" role="img" aria-label="Golden fish oil softgels on a wooden table" style="top:3693px;height:429px;background:linear-gradient(100deg,#6a6040,#7a6a3c 40%,#4a3c28 75%,#3a2e20)"></div>
<div class="abs banner-copy" style="top:3752px">
  <h2>Lorem Ipsum</h2>
  <p>Sed ut perspiciatis iste natus error sit<br>voluptatem accusantium</p>
</div>
<div class="abs countdown">
  <div><span>45</span><span>DAYS</span></div>
  <div><span>19</span><span>HRS</span></div>
  <div><span>23</span><span>MINS</span></div>
  <div><span>08</span><span>SEC</span></div>
</div>
<div class="abs btn-outline" style="left:912px;top:4003px;width:176px;height:64px;color:var(--white)">SHOP NOW</div>

<!-- newsletter -->
<div class="abs" role="img" aria-label="Hand holding softgel capsules on a pink background" style="left:110px;top:4215px;width:490px;height:369px;background:linear-gradient(150deg,#e4a6a0,#d88e88 55%,#c9a070)"></div>
<h2 class="abs display center" style="left:600px;top:4268px;width:510px;font-size:17px">Get In Touch</h2>
<p class="abs center" style="left:600px;top:4322px;width:510px;font-size:15px;color:var(--ink)">WE SEND LATEST NEWS &amp; OFFERS INFORMATION TO YOU.</p>
<div class="abs field" style="left:683px;top:4376px;width:342px;height:58px">EMAIL</div>
<div class="abs btn-plain" style="left:778px;top:4469px;width:154px;height:60px">SUBSCRIBE</div>

<!-- footer -->
<footer class="abs footer"></footer>
<div class="abs brand" style="left:110px;top:4740px"><div class="brand-dot"></div><div class="brand-name">Kelmo</div></div>
<p class="abs" style="left:110px;top:4820px;width:320px;font-size:14px;line-height:31px;color:var(--ink)">Sed ut perspiciatis unde omnis iste natus error sit voluptatem accusantium doloremque laudantium, totam rem aperiam.</p>
<div class="abs social" style="left:110px;top:4935px"></div>
<div class="abs social" style="left:157px;top:4935px"></div>
<div class="abs social" style="left:204px;top:4935px"></div>

<h3 class="abs display foot-title" style="left:488px;top:4722px">About Us</h3>
<span class="abs foot-link" style="left:488px;top:4775px">ABOUT US</span>
<span class="abs foot-link" style="left:488px;top:4815px">FAQ</span>
<span class="abs foot-link" style="left:488px;top:4854px">CONTACT US</span>

<h3 class="abs display foot-title" style="left:675px;top:4722px">Quick Buy</h3>
<span class="abs foot-link" style="left:675px;top:4775px">LOREM IPSUM</span>
<span class="abs foot-link" style="left:675px;top:4815px">LOREM IPSUM</span>
<span class="abs foot-link" style="left:675px;top:4854px">LOREM IPSUM</span>

<h3 class="abs display foot-title" style="left:855px;top:4722px">Subscribe Email</h3>
<p class="abs" style="left:855px;top:4760px;width:235px;font-size:14px;line-height:32px;color:var(--ink);text-align:justify">Sed ut perspiciatis unde omnis iste natus error sit voluptatem</p>
<div class="abs field" style="left:855px;top:4837px;width:253px;height:47px;font-size:14px">EMAIL</div>
<div class="abs btn-plain" style="left:861px;top:4910px;width:114px;height:43px;font-size:11px">SUBSCRIBE</div>

<div class="abs" style="left:110px;top:5014px;width:980px;height:1px;background:var(--line)"></div>
<p class="abs" style="left:114px;top:5044px;font-size:14px;color:var(--ink)">© 2023, KELMO &nbsp;I ALL RIGHTS RESERVED.</p>
<div class="abs" style="left:892px;top:5046px;display:flex;gap:5px">
  <div class="pay" style="background:#c9c3d6"></div>
  <div class="pay" style="background:#e7b6a6"></div>
  <div class="pay" style="background:#8fb0dc"></div>
  <div class="pay" style="background:#b7c6e0"></div>
  <div class="pay" style="background:#d0c8dc"></div>
  <div class="pay" style="background:#e8c9a0"></div>
</div>

</body>
</html>
```